Brovo like IOS/Android app for Okinawa Island - TaruSeeker

TaruSeeker is the name of the app
The closest thing that I can relate this app to is a region specific Brovo app. The app is for the island of Okinawa and is geared towards English speaking travelers. The style of app that I prefer is a look and feel similar to that of the new Nestory app, color should also be similar if not the same as the nestory app.

The app needs to have the following screens

LOGIN SCREEN
1. App login page with a login for chatterly button or create an account option. Personally I would like an image in the background with a real beachy feel, but don't do this if it messes with your design.

2. Depending on the choice of login there will need to be a second login screen to create the account. Nestory does this nicely.

PRIMARY HOME
primary page similar to the primary layout when you get into the nestory app.
This page is kind of like the home page of the app and should include the following items:
search field
upcoming events
popular things to do
featured restaurants
Featured Places to stay
area guides
Moving here
(this will allow the person to select, housing agencies, auto dealers, schools etc) These are essentially just quick searches.
Each selection should be listed so that the user can swipe to the left or right in order to view more listings under the categories listed above. It will not be the full list but rather a sample.

SIDEBAR POPOUT MENU
Popout sidebar that contains the following selections
Places to Eat
Things to do
Attractions
Beaches
Shop
Farmers Markets
Places to Stay
Schools & DayCare
Housing
Auto
Events
Account settings
Add a business

LIST VIEW
4. List view page for whatever category the user selected. This will show all the listings for the specific category: The top should also have the featured listings for that category

INDIVIDUAL LISTING
5. Listing page
This will include photos, description, hours, map(this can be a button to view the map or the map), Reviews with a leave a review option

AREA GUIDES
6. Area Guides. This is where the user will be able to select a specific area and learn about it. It should include an area where there can be a description, photos with a hero photo image, a map, popular local attractions or things to do, best restaurants in the area, places to stay etc.

PROFILE PAGE
7. Profile page for the user where they can make any updates they need to

Every page but the listing page should include the search bar. When the user clicks in it they should be able to see a drop down of quick select searches or run a regular search.

Logo
I have attached a logo that was made that needs a redesign. The map marker contains the logo for Okinawa within it so it does need to be similar.

If you have any questions or need clarification please send me a message. I will respond promptly.
Thank you,

Industry/Entity Type

Android

Logo Text

TaruSeeker

```html
<!DOCTYPE html>
<html lang="en">
<head>
<meta charset="utf-8">
<title>TaruSeeker – Home</title>
<link href="https://fonts.googleapis.com/css2?family=Figtree:wght@400;500;600;700&display=swap" rel="stylesheet">
<style>
:root{
  --bg:#efefef;
  --screen:#ffffff;
  --accent:#e8576a;
  --ink:#1f1f1f;
  --muted:#9a9a9a;
  --line:#ececec;
  --shade:rgba(0,0,0,.55);
}
*{box-sizing:border-box;margin:0;padding:0}
html,body{width:1200px;height:1200px;overflow:hidden;background:var(--bg);font-family:"Figtree",sans-serif;color:var(--ink)}
.screen{position:absolute;left:446px;top:38px;width:309px;height:1125px;background:var(--screen);overflow:hidden;box-shadow:0 6px 30px rgba(0,0,0,.08)}
.abs{position:absolute}
.status{left:0;top:0;width:100%;height:16px;font-size:9.5px;font-weight:500}
.status .carrier{position:absolute;left:6px;top:3px}
.status .time{position:absolute;left:0;right:0;top:3px;text-align:center;font-weight:600}
.status .battery{position:absolute;right:6px;top:3px;display:flex;align-items:center;gap:3px}
.battery i{display:inline-block;width:20px;height:8px;border:1px solid #111;border-radius:2px;background:#111;box-shadow:inset 0 0 0 1px #fff}
.header{left:0;top:16px;width:100%;height:37px;border-bottom:1px solid var(--accent)}
.menu-btn{position:absolute;left:14px;top:14px;width:15px;height:12px}
.brand{position:absolute;left:112px;top:9px;display:flex;align-items:center;gap:6px;font-size:13.6px;font-weight:600;color:var(--ink)}
.brand .dot{width:19px;height:19px;border-radius:50%;background:var(--accent)}
.search{left:0;top:53px;width:100%;height:37px;border-bottom:1px solid var(--line);display:flex;align-items:center;padding-left:14px;gap:8px;font-size:10.5px;color:var(--muted)}
.section-title{left:14px;font-size:19px;font-weight:600;color:var(--accent);letter-spacing:.1px}
.sub-title{left:14px;font-size:11px;font-weight:700;color:var(--ink)}
.photo{position:absolute;border-radius:2px;overflow:hidden;background:var(--tone);box-shadow:0 1px 3px rgba(0,0,0,.25)}
.photo::after{content:"";position:absolute;inset:0;background:linear-gradient(180deg,rgba(0,0,0,.05) 30%,var(--shade))}
.photo .label{position:absolute;left:0;right:0;z-index:1;text-align:center;color:#fff;font-weight:600;line-height:1.25}
.hero .label{font-size:14.4px;font-weight:500}
.hero .date{position:absolute;left:0;right:0;z-index:1;text-align:center;color:var(--accent);font-size:9px}
.tile .label{font-size:9.4px;font-weight:500;bottom:10px;white-space:nowrap}
.quick{display:flex;align-items:center;justify-content:center}
.quick::after{background:rgba(30,40,60,.45)}
.quick .label{position:relative;font-size:9.2px;font-weight:500}
</style>
</head>
<body>
<div class="screen">
  <div class="abs status">
    <span class="carrier">●●●○○ Carrier</span>
    <span class="time">4:21 PM</span>
    <span class="battery">100% <i></i></span>
  </div>

  <div class="abs header">
    <svg class="menu-btn" viewBox="0 0 15 12"><g stroke="#e8576a" stroke-width="1.1"><line x1="0" y1="1" x2="15" y2="1"/><line x1="0" y1="6" x2="15" y2="6"/><line x1="0" y1="11" x2="15" y2="11"/></g></svg>
    <div class="brand"><span class="dot"></span>TaruSeeker</div>
  </div>

  <div class="abs search">
    <svg width="12" height="12" viewBox="0 0 12 12"><circle cx="5" cy="5" r="4" fill="none" stroke="#b0b0b0" stroke-width="1"/><line x1="8" y1="8" x2="11.5" y2="11.5" stroke="#b0b0b0" stroke-width="1"/></svg>
    Search for locations or events
  </div>

  <h2 class="abs section-title" style="top:105px">Upcoming events</h2>
  <div class="photo hero" style="left:14px;top:142px;width:280px;height:115px;--tone:linear-gradient(135deg,#2c3850,#8a3b3c 45%,#4a4f5e)" role="img" aria-label="Festival drummers performing at night">
    <span class="label" style="top:67px">Eisa Festival 2016</span>
    <span class="date" style="top:89px">Sep 4, 2016</span>
  </div>
  <div class="photo" style="left:301px;top:142px;width:20px;height:115px;--tone:linear-gradient(180deg,#8fa3b8,#c0a38a)" role="img" aria-label="Next event photo"></div>

  <h2 class="abs section-title" style="top:282px">Popular things to do</h2>
  <div class="photo hero" style="left:14px;top:318px;width:280px;height:116px;--tone:linear-gradient(135deg,#c9b21e,#7d8a2a 50%,#3d6d4a)" role="img" aria-label="Children playing on an inflatable slide">
    <span class="label" style="top:85px">Summer Adventure School</span>
  </div>
  <div class="photo" style="left:301px;top:318px;width:20px;height:116px;--tone:#1e2430" role="img" aria-label="Next activity photo"></div>

  <h2 class="abs section-title" style="top:459px">Featured</h2>
  <h3 class="abs sub-title" style="top:496px">Restaurants</h3>
  <div class="photo tile" style="left:14px;top:518px;width:99px;height:90px;--tone:linear-gradient(135deg,#d8d2c8,#a2646a)" role="img" aria-label="Grilled meat dishes on a table"><span class="label">Yakiniku<br>House Sora</span></div>
  <div class="photo tile" style="left:121px;top:518px;width:99px;height:90px;--tone:linear-gradient(135deg,#c98b4a,#b2433a 55%,#d7b37a)" role="img" aria-label="Sashimi and noodle dishes"><span class="label">Okinawa Kaze<br>Japanese Restaur...</span></div>
  <div class="photo tile" style="left:229px;top:518px;width:99px;height:90px;--tone:linear-gradient(135deg,#2a221c,#8a6a3e)" role="img" aria-label="Lantern-lit restaurant interior"><span class="label" style="text-align:left;left:16px">Hoshizora Izakaya</span></div>

  <h3 class="abs sub-title" style="top:627px">Places to stay</h3>
  <div class="photo tile" style="left:14px;top:648px;width:99px;height:90px;--tone:linear-gradient(180deg,#cfcac2,#4b4a4a)" role="img" aria-label="Hotel entrance facade"><span class="label">Coralline Hotel</span></div>
  <div class="photo tile" style="left:121px;top:648px;width:99px;height:90px;--tone:linear-gradient(180deg,#4a86b8,#2f6a4a 55%,#5da3a8)" role="img" aria-label="Beach with palm trees"><span class="label">Hotel Tide Beach</span></div>
  <div class="photo tile" style="left:229px;top:648px;width:99px;height:90px;--tone:linear-gradient(180deg,#3d7fd0,#3b5f6e 60%,#6ab8c0)" role="img" aria-label="Resort terrace with pool"><span class="label" style="text-align:left;left:8px">Sango Terrace Bea</span></div>

  <h2 class="abs section-title" style="top:764px">Area Guides</h2>
  <div class="photo tile" style="left:14px;top:798px;width:99px;height:91px;--tone:linear-gradient(180deg,#5aa0d6,#9ab6b8 55%,#b59a7a)" role="img" aria-label="Seaside promenade"><span class="label">Central Area</span></div>
  <div class="photo tile" style="left:121px;top:798px;width:99px;height:91px;--tone:linear-gradient(180deg,#c6ccc6,#4e7a44)" role="img" aria-label="Forested hills in mist"><span class="label">Northern Area</span></div>
  <div class="photo tile" style="left:229px;top:798px;width:99px;height:91px;--tone:linear-gradient(180deg,#9aa0a4,#4a5a3a)" role="img" aria-label="City street with buildings"><span class="label" style="text-align:left;left:28px">Naha City</span></div>

  <h2 class="abs section-title" style="top:918px">Moving Here</h2>
  <div class="photo quick" style="left:14px;top:953px;width:89px;height:58px;--tone:linear-gradient(135deg,#4d5c72,#2c3a52)" role="img" aria-label="Cars on a dealer lot"><span class="label">Auto Dealers</span></div>
  <div class="photo quick" style="left:110px;top:953px;width:88px;height:58px;--tone:linear-gradient(180deg,#8c96a4,#3b4756)" role="img" aria-label="Apartment buildings"><span class="label">Housing<br>Agencies</span></div>
  <div class="photo quick" style="left:206px;top:953px;width:89px;height:58px;--tone:linear-gradient(135deg,#aeb6c4,#4a5872)" role="img" aria-label="Doctor at work"><span class="label">Healthcare</span></div>
  <div class="photo quick" style="left:14px;top:1019px;width:89px;height:58px;--tone:linear-gradient(135deg,#6c6a6e,#4f6e7e)" role="img" aria-label="Students in a classroom"><span class="label">Schools</span></div>
  <div class="photo quick" style="left:110px;top:1019px;width:88px;height:58px;--tone:linear-gradient(180deg,#7a8496,#3a4458)" role="img" aria-label="Shopping street"><span class="label">Shop</span></div>
  <div class="photo quick" style="left:206px;top:1019px;width:89px;height:58px;--tone:linear-gradient(135deg,#9ea4b2,#505a70)" role="img" aria-label="People working in an office"><span class="label">To Work</span></div>
</div>
</body>
</html>
```